RTavenor Business Cards & Letterhead

I have a logo but need a design for some new business cards. We are a Design-Build Firm that specializes in the design and construction of commercial projects.
the cards need to be professional. no cartoon stuff.
i would like to have the cards in AI format so I can update the card as needed. Logo is provided.
Our Address is: 4187 Marlowe Ct. Ashford Hollow, Wrenfield 27614

```html
<!DOCTYPE html>
<html lang="en">
<head>
<meta charset="utf-8">
<title>RTavenor Business Card</title>
<link rel="stylesheet" href="https://fonts.googleapis.com/css2?family=Montserrat:wght@700;800&family=Open+Sans:wght@400;600&display=swap">
<style>
  :root {
    --backdrop: #4a4a49;
    --card: #161616;
    --card-deep: #0d0d0d;
    --accent: #1565b8;
    --accent-bright: #1a7bd0;
    --ink: #ffffff;
    --ink-soft: #e6e6e6;
  }
  * { box-sizing: border-box; margin: 0; padding: 0; }
  html, body { width: 1200px; height: 801px; overflow: hidden; }
  body {
    background: var(--backdrop);
    font-family: "Open Sans", Arial, sans-serif;
    display: flex;
    align-items: center;
    justify-content: center;
    gap: 40px;
  }
  .card {
    position: relative;
    width: 540px;
    height: 310px;
    background: var(--card);
    border-radius: 16px;
    border-bottom: 4px solid var(--accent);
    box-shadow: 0 14px 30px rgba(0,0,0,0.35);
    overflow: hidden;
  }
  .card__accent {
    position: absolute;
    left: 0;
    top: 122px;
    width: 14px;
    height: 30px;
    background: var(--accent);
  }
  .card__info {
    position: absolute;
    left: 36px;
    top: 34px;
    color: var(--ink);
  }
  .brand {
    display: flex;
    align-items: center;
    gap: 10px;
    margin-bottom: 22px;
  }
  .brand__square {
    width: 22px;
    height: 22px;
    background: var(--accent);
  }
  .brand__name {
    font-family: "Montserrat", Arial, sans-serif;
    font-weight: 800;
    font-size: 32px;
    letter-spacing: 0.5px;
    color: var(--ink);
  }
  .person__name {
    font-family: "Montserrat", Arial, sans-serif;
    font-weight: 700;
    font-size: 18px;
    color: var(--accent-bright);
    letter-spacing: 0.3px;
  }
  .person__title {
    font-size: 13px;
    color: var(--ink-soft);
    margin-bottom: 18px;
  }
  .contact { list-style: none; margin-bottom: 16px; }
  .contact__item {
    display: flex;
    align-items: center;
    gap: 8px;
    font-size: 13px;
    line-height: 19px;
    color: var(--ink-soft);
  }
  .contact__icon { width: 11px; height: 11px; fill: var(--accent-bright); }
  .address { font-style: normal; font-size: 13px; line-height: 19px; color: var(--ink-soft); }
  .emblem {
    position: absolute;
    right: 44px;
    top: 50%;
    width: 190px;
    height: 190px;
    transform: translateY(-50%);
    border-radius: 22px;
    background: linear-gradient(135deg, #3a3a3a 0%, #1b1b1b 45%, var(--card-deep) 100%);
    box-shadow: inset 0 0 0 1px rgba(255,255,255,0.06);
  }
  .card--back .emblem { right: 50%; transform: translate(50%, -50%); }
</style>
</head>
<body>
  <section class="card card--front" aria-label="Business card front">
    <div class="card__accent"></div>
    <div class="card__info">
      <div class="brand">
        <span class="brand__square"></span>
        <span class="brand__name">RTAVENOR</span>
      </div>
      <p class="person__name">DANIEL WHITCOMBE</p>
      <p class="person__title">Managing Director</p>
      <ul class="contact">
        <li class="contact__item">
          <svg class="contact__icon" viewBox="0 0 24 24"><path d="M6.6 10.8a15 15 0 0 0 6.6 6.6l2.2-2.2c.3-.3.7-.4 1-.2 1.1.4 2.3.6 3.6.6.6 0 1 .4 1 1V20c0 .6-.4 1-1 1A17 17 0 0 1 3 4c0-.6.4-1 1-1h3.5c.6 0 1 .4 1 1 0 1.3.2 2.5.6 3.6.1.3 0 .7-.2 1z"/></svg>
          555 019 2748
        </li>
        <li class="contact__item">
          <svg class="contact__icon" viewBox="0 0 24 24"><path d="M2 5h20v14H2z M2 5l10 8 10-8" /></svg>
          hello@rtavenorbuild.com
        </li>
        <li class="contact__item">
          <svg class="contact__icon" viewBox="0 0 24 24"><circle cx="12" cy="12" r="10"/></svg>
          www.rtavenorbuild.com
        </li>
      </ul>
      <address class="address">4187 Marlowe Ct. Ashford Hollow,<br>Wrenfield 27614</address>
    </div>
    <div class="emblem" role="img" aria-label="Large glossy brand emblem decoration"></div>
  </section>

  <section class="card card--back" aria-label="Business card back">
    <div class="emblem" role="img" aria-label="Large glossy brand emblem decoration"></div>
  </section>
</body>
</html>
```